New Business Card Design Project

Use the flyer uploaded and website www.brightoakbuilders.com for inspiration.
List Our Services on Backside of business cards
Marcus Delling
Harborline Builders Inc.
Licensed General Contractors
858-471-6093

Contact Information for Business Card

Use the flyer uploaded and website www.brightoakbuilders.com for inspiration. List Our Services on Backside of business cards Marcus Delling Harborline Builders Inc. Licensed General Contractors 858-471-6093

```html
<!DOCTYPE html>
<html lang="en">
<head>
<meta charset="utf-8">
<title>Harborline Builders – Business Card</title>
<link href="https://fonts.googleapis.com/css2?family=Marcellus&family=Montserrat:wght@400;500&display=swap" rel="stylesheet">
<style>
  :root {
    --backdrop: #2b2b2c;
    --card: #1b1c1e;
    --card-edge: #26272a;
    --ink: #f4f4f4;
    --ink-soft: #d9d9d9;
  }
  * { box-sizing: border-box; margin: 0; padding: 0; }
  html, body { width: 1200px; height: 900px; overflow: hidden; background: var(--backdrop); }
  .canvas { position: relative; width: 1200px; height: 900px; }
  .card {
    position: absolute; left: 240px; width: 720px; height: 411px;
    background: linear-gradient(135deg, var(--card) 0%, var(--card-edge) 100%);
    border-radius: 14px; box-shadow: 0 10px 28px rgba(0,0,0,.45);
    color: var(--ink);
  }
  .card--front { top: 28px; }
  .card--back { top: 462px; }

  .brand-name {
    font-family: "Marcellus", serif; font-weight: 400;
    letter-spacing: 2px; text-transform: uppercase; color: var(--ink);
  }
  .card--front .brand {
    position: absolute; inset: 0; display: flex; align-items: center; justify-content: center;
  }
  .card--front .brand-name { font-size: 40px; }

  .card--back .brand {
    position: absolute; left: 0; top: 0; width: 360px; height: 300px;
    display: flex; align-items: center; justify-content: center;
  }
  .card--back .brand-name { font-size: 27px; }

  .divider {
    position: absolute; left: 378px; top: 70px; width: 1.5px; height: 190px; background: var(--ink-soft);
  }
  .contact { position: absolute; left: 410px; top: 72px; }
  .contact__name { font-family: "Marcellus", serif; font-size: 28px; letter-spacing: 1.5px; text-transform: uppercase; }
  .contact__title { font-family: "Montserrat", sans-serif; font-size: 15px; letter-spacing: .5px; margin-top: 2px; color: var(--ink-soft); }
  .contact__list { list-style: none; margin-top: 26px; }
  .contact__item {
    display: flex; align-items: center; gap: 12px;
    font-family: "Montserrat", sans-serif; font-size: 16px; letter-spacing: .6px; margin-bottom: 10px;
  }
  .contact__item svg { width: 14px; height: 14px; flex: none; }

  .footer-rule {
    position: absolute; left: 0; right: 0; bottom: 70px;
    display: flex; align-items: center; gap: 14px;
  }
  .footer-rule::before, .footer-rule::after { content: ""; flex: 1; height: 1.5px; background: var(--ink-soft); }
  .footer-rule span { font-family: "Montserrat", sans-serif; font-size: 16px; letter-spacing: .8px; }
</style>
</head>
<body>
<main class="canvas">
  <section class="card card--front">
    <div class="brand"><span class="brand-name">Harborline Builders</span></div>
  </section>

  <section class="card card--back">
    <div class="brand"><span class="brand-name">Harborline Builders</span></div>
    <div class="divider"></div>
    <div class="contact">
      <h1 class="contact__name">Marcus Delling</h1>
      <p class="contact__title">Licensed General Contractors</p>
      <ul class="contact__list">
        <li class="contact__item">
          <svg viewBox="0 0 24 24" fill="none" stroke="currentColor" stroke-width="2.4"><path d="M5 3h4l2 5-2.5 1.5a11 11 0 0 0 6 6L16 13l5 2v4a2 2 0 0 1-2 2A17 17 0 0 1 3 5a2 2 0 0 1 2-2z"/></svg>
          858-471-6093
        </li>
        <li class="contact__item">
          <svg viewBox="0 0 24 24" fill="currentColor"><path d="M2 5h20v14H2z"/><path d="M2 5l10 8 10-8" stroke="#1b1c1e" stroke-width="2" fill="none"/></svg>
          info@brightoakbuilders.com
        </li>
        <li class="contact__item">
          <svg viewBox="0 0 24 24" fill="none" stroke="currentColor" stroke-width="2.2"><circle cx="12" cy="12" r="10"/><path d="M2 12h20M12 2c3 3 3 17 0 20M12 2c-3 3-3 17 0 20"/></svg>
          www.brightoakbuilders.com
        </li>
      </ul>
    </div>
    <div class="footer-rule"><span>Harborline Builders Inc.</span></div>
  </section>
</main>
</body>
</html>
```